Consulting Company PowerPoint Template Design

We are looking for an updated PowerPoint template design or our 55 person energy consulting firm (K7) based in San Francisco (www.kseven-example.com). We would like two versions of the same PowerPoint template in a 16:9 and 4:3 format with our existing logo.

We have an existing color scheme and template and are seeking your help to polish/update the template design for wide format and create a flexible template that is easy to use with content from Excel and Word. Our current template, and a couple of examples that we like are attached.

Specific requests include:

• Dark background for slide title
• A narrow section header
• Maximizing white space for content
• A limited number of well designed Master template layouts to choose from
• A selection of title and section header slides that are not San Francisco specific with some variety to chose from ideally with a focus on energy or nature, graphics/visuals.

For examples of energy specific templates see:
https://www.brightslidehub.example/energy/powerpoint-templates/0.html

Requirements
Must have
• Must use our logo but open to other designs, fonts, and styles for the PowerPoint template.
• Please use our existing color scheme found in the attached Excel file.
• Also we would like the ability to easily copy and paste from our existing/original template to the new template. In other words we would like backward compatibility to apply the new template format to our old PowerPoints that use our existing template.

```html
<!DOCTYPE html>
<html lang="en">
<head>
<meta charset="utf-8">
<title>K7 – Images Slide</title>
<link href="https://fonts.googleapis.com/css2?family=Titillium+Web:wght@400;600;700&display=swap" rel="stylesheet">
<style>
  :root {
    --navy: #0b5072;
    --gold: #c4a66b;
    --gold-light: #cdb27c;
    --gold-title: #c9a96a;
    --white: #ffffff;
  }
  html, body {
    margin: 0;
    padding: 0;
    width: 1200px;
    height: 903px;
    overflow: hidden;
    background: var(--navy);
  }
  .slide {
    position: relative;
    width: 1200px;
    height: 903px;
    overflow: hidden;
    background: var(--navy);
    font-family: "Titillium Web", sans-serif;
  }
  .slide__backdrop {
    position: absolute;
    inset: 0;
    width: 1200px;
    height: 903px;
  }
  .slide__title {
    position: absolute;
    left: 42px;
    top: 24px;
    margin: 0;
    font-size: 42px;
    font-weight: 700;
    color: var(--gold-title);
    letter-spacing: 0.2px;
  }
  .slide__body {
    position: absolute;
    left: 42px;
    top: 122px;
    width: 700px;
  }
  .slide__body p {
    margin: 0 0 31px;
    font-size: 20.5px;
    line-height: 33.4px;
    font-weight: 400;
    color: var(--white);
  }
  .brand {
    position: absolute;
    top: 12px;
    right: 15px;
    display: flex;
    align-items: center;
    gap: 12px;
  }
  .brand__name {
    font-size: 30px;
    font-weight: 700;
    color: var(--navy);
  }
  .brand__dot {
    width: 68px;
    height: 68px;
    border-radius: 50%;
    background: var(--navy);
    box-shadow: 0 0 0 4px var(--white) inset;
  }
  .slide__footer {
    position: absolute;
    right: 20px;
    bottom: 12px;
    margin: 0;
    font-size: 27px;
    font-weight: 700;
    color: var(--white);
  }
</style>
</head>
<body>
  <div class="slide">
    <svg class="slide__backdrop" viewBox="0 0 1200 903" aria-hidden="false">
      <defs>
        <linearGradient id="goldWash" x1="0" y1="0" x2="0.4" y2="1">
          <stop offset="0" stop-color="#c8aa70"/>
          <stop offset="0.6" stop-color="#c4a66b"/>
          <stop offset="1" stop-color="#bfa064"/>
        </linearGradient>
      </defs>
      <polygon points="967,0 1200,0 1200,903 330,903" fill="url(#goldWash)"
               role="img" aria-label="Faint photograph of high-voltage transmission towers and power lines"/>
    </svg>

    <h1 class="slide__title">Images Title Here</h1>

    <div class="slide__body">
      <p>Lemon drops oat cake oat cake sugar plum sweet gingerbread choc-<br>olate oreo cake jelly plum ginger bread. Lemon drops oat cake oat<br>cake sugar plum sweet gingerbread chocolate cake cake sweet gin-<br>gerbread oreo.</p>
      <p>Lemon drops oat cake oat cake sugar plum sweet gingerbread<br>chocolate oreo cake jelly plum ginger bread. Lemon<br>drops oat cake oat cake sugar plum sweet<br>gingerbread chocolate cake cake sweet</p>
      <p>Lemon drops oat cake oat cake sugar plum<br>&nbsp;sweet gingerbread chocolate oreo<br>&nbsp;cake jelly plum ginger bread.<br>Lemon drops oat cake oat cake sugar<br>plum sweet&nbsp; gingerbread chocolate<br>cake cake sweet</p>
    </div>

    <div class="brand">
      <span class="brand__name">K7</span>
      <span class="brand__dot"></span>
    </div>

    <p class="slide__footer">Kinetic+Veldt Energy Economics</p>
  </div>
</body>
</html>
```